Revamp Business Card for Landscaping/Gardening Service Provider

We are a small landscaping company that is in desperate need of someone to recreate our business card. I have attached what we are currently using along with the logo.

These are the services we specialize in:
- lawn service
- mow, edge and clean
- fertilizing
- prune and trim
- seed and topping
- planting
- irrigation sprinklers

We don't want the front to be too busy but we do want the bulk of the information to be on this side such as the logo (recreate if possible), what we do and maybe the contact information. The back we would like it to be lined if possible, to add notes or even provide quotes for customers. If you feel you've got the talent to take on this project, please send in your design.

Thank you

```html
<!DOCTYPE html>
<html lang="en">
<head>
<meta charset="utf-8">
<title>Ruben Ortega Gardening — Business Card</title>
<link rel="stylesheet" href="https://fonts.googleapis.com/css2?family=Open+Sans:wght@400;600;700&display=swap">
<style>
  :root {
    --page-bg: #2b2d31;
    --leaf-dark: #3f6b2a;
    --leaf-mid: #5f9a3a;
    --leaf-light: #8cc152;
    --lawn: #6fb33a;
    --bloom-red: #d8412e;
    --bloom-yellow: #e3c23c;
    --paper: #ffffff;
    --overlay-green: rgba(86, 150, 46, 0.82);
    --overlay-white: rgba(255, 255, 255, 0.72);
    --line: rgba(63, 107, 42, 0.55);
  }
  * { box-sizing: border-box; margin: 0; padding: 0; }
  html, body {
    width: 1200px; height: 900px; overflow: hidden;
    background: var(--page-bg);
    font-family: "Open Sans", Arial, sans-serif;
  }
  .sheet {
    width: 1200px; height: 900px;
    display: flex; flex-direction: column; align-items: center; justify-content: center;
    gap: 40px;
  }
  .card {
    position: relative;
    width: 700px; height: 400px;
    overflow: hidden;
    border-radius: 4px;
    box-shadow: 0 10px 30px rgba(0,0,0,0.45);
  }
  .garden-photo {
    position: absolute; inset: 0;
    background:
      radial-gradient(ellipse at 72% 55%, rgba(216,65,46,0.55) 0 8%, transparent 22%),
      radial-gradient(ellipse at 62% 75%, rgba(227,194,60,0.5) 0 7%, transparent 20%),
      radial-gradient(ellipse at 10% 80%, rgba(201,70,110,0.5) 0 6%, transparent 16%),
      linear-gradient(160deg, #cfd6c8 0%, #9fbf7a 22%, var(--lawn) 45%, var(--leaf-mid) 70%, var(--leaf-dark) 100%);
  }
  /* brand block */
  .brand {
    position: absolute;
    width: 190px; height: 150px;
    background: var(--leaf-dark);
    border: 4px solid var(--paper);
    display: flex; align-items: center; justify-content: center; gap: 10px;
    padding: 14px;
  }
  .brand-mark {
    width: 12px; height: 12px; background: var(--paper); flex: none;
  }
  .brand-name {
    color: var(--paper);
    font-weight: 700;
    font-size: 21px;
    line-height: 1.15;
    text-transform: uppercase;
    letter-spacing: 0.5px;
  }
  /* front */
  .card-front .brand { left: 48px; top: 36px; }
  .contact-list {
    position: absolute; left: 48px; top: 212px;
    list-style: none;
    display: flex; flex-direction: column; gap: 7px;
  }
  .contact-item {
    display: flex; align-items: center; gap: 8px;
    color: var(--paper);
    font-size: 13px; font-weight: 600;
    text-shadow: 0 1px 2px rgba(0,0,0,0.45);
  }
  .contact-icon { width: 14px; height: 14px; flex: none; }
  .services-panel {
    position: absolute; right: 0; top: 0; bottom: 0;
    width: 380px;
    background: var(--overlay-green);
    padding: 40px 40px 30px 46px;
    color: var(--paper);
  }
  .services-title {
    font-size: 20px; font-weight: 700; line-height: 1.25;
    padding-bottom: 10px;
    border-bottom: 2px solid var(--paper);
    margin-bottom: 14px;
  }
  .services-list { list-style: none; }
  .services-list li {
    font-size: 17px; font-weight: 400; line-height: 1.6;
  }
  .services-list li::before { content: "- "; }
  /* back */
  .notes-panel {
    position: absolute; left: 0; top: 0; bottom: 0;
    width: 330px;
    background: var(--overlay-white);
  }
  .card-back .brand { left: 70px; top: 30px; }
  .note-lines {
    position: absolute; left: 40px; right: 30px; top: 215px;
    display: flex; flex-direction: column; gap: 36px;
  }
  .note-line { height: 0; border-bottom: 1.5px solid var(--line); }
  .back-strip {
    position: absolute; right: 0; bottom: 0;
    width: 370px; height: 120px;
    background: var(--overlay-green);
  }
</style>
</head>
<body>
<main class="sheet">
  <section class="card card-front" aria-label="Business card front">
    <div class="garden-photo" role="img" aria-label="Photo of a lush garden with lawn, green shrubs and red and yellow flower beds"></div>
    <div class="brand">
      <span class="brand-mark"></span>
      <span class="brand-name">Ruben Ortega Gardening</span>
    </div>
    <ul class="contact-list">
      <li class="contact-item">
        <svg class="contact-icon" viewBox="0 0 24 24" fill="#fff"><path d="M6.6 10.8a15.1 15.1 0 0 0 6.6 6.6l2.2-2.2a1 1 0 0 1 1-.25 11.4 11.4 0 0 0 3.6.57 1 1 0 0 1 1 1V20a1 1 0 0 1-1 1A17 17 0 0 1 3 4a1 1 0 0 1 1-1h3.5a1 1 0 0 1 1 1c0 1.25.2 2.45.57 3.6a1 1 0 0 1-.25 1z"/></svg>
        805.555.0142
      </li>
      <li class="contact-item">
        <svg class="contact-icon" viewBox="0 0 24 24" fill="none" stroke="#fff" stroke-width="2"><rect x="3" y="5" width="18" height="14" rx="1"/><path d="M3 6l9 7 9-7"/></svg>
        info@ortegagardening.com
      </li>
      <li class="contact-item">
        <svg class="contact-icon" viewBox="0 0 24 24" fill="none" stroke="#fff" stroke-width="2"><circle cx="12" cy="12" r="9"/><path d="M3 12h18M12 3c3 3 3 15 0 18M12 3c-3 3-3 15 0 18"/></svg>
        www.ortegagardening.com
      </li>
    </ul>
    <div class="services-panel">
      <h2 class="services-title">These are the services<br>we specialize in:</h2>
      <ul class="services-list">
        <li>lawn service</li>
        <li>mow, edge and clean</li>
        <li>fertilizing</li>
        <li>prune and trim</li>
        <li>seed and topping</li>
        <li>planting</li>
        <li>irrigation sprinklers</li>
      </ul>
    </div>
  </section>

  <section class="card card-back" aria-label="Business card back">
    <div class="garden-photo" role="img" aria-label="Photo of a garden path with lawn and colourful flower borders"></div>
    <div class="notes-panel"></div>
    <div class="back-strip"></div>
    <div class="brand">
      <span class="brand-mark"></span>
      <span class="brand-name">Ruben Ortega Gardening</span>
    </div>
    <div class="note-lines">
      <div class="note-line"></div>
      <div class="note-line"></div>
      <div class="note-line"></div>
      <div class="note-line"></div>
    </div>
  </section>
</main>
</body>
</html>
```